Canadian Christian Church needs design for new sermon series

A graphic design for our series and an invitation card to invite people to the series. Check design brief for more detailed information. Target audience: young families and young adults. Looking for a creative design that will get people's attention and create interest. See design brief for copy of design purchased for previous series.
Updates
entered Apr 4 incorrectly. Need a week to receive and review designs, and today is Apr 2/19. Thanks!
Target Market(s)
young families and young adults
Colors
Designer to choose colors to be used in the design.
Look and feel

```html
<!DOCTYPE html>
<html lang="en">
<head>
<meta charset="utf-8">
<title>Messy – Sermon Series Invitation</title>
<link href="https://fonts.googleapis.com/css2?family=Open+Sans:wght@600;700;800&family=Noto+Serif:wght@700&family=Comfortaa:wght@500&family=Oswald:wght@300&display=swap" rel="stylesheet">
<style>
  :root {
    --page: #ece8e3;
    --plum-dark: #3a2a38;
    --plum-mid: #5e4650;
    --plum-soft: #7a6265;
    --stone: #8a7f78;
    --leather: #8a4a32;
    --white: #ffffff;
    --text-soft: #f3ecee;
    --accent: #e9932f;
  }
  * { margin: 0; padding: 0; box-sizing: border-box; }
  html, body { width: 1200px; height: 1200px; overflow: hidden; }
  body { background: var(--page); position: relative; font-family: "Open Sans", sans-serif; color: var(--white); }

  .card { position: absolute; left: 263px; width: 674px; height: 530px; overflow: hidden; box-shadow: 0 6px 14px rgba(0,0,0,.25); }
  .card--front { top: 44px; }
  .card--back { top: 625px; background: radial-gradient(ellipse at 40% 30%, var(--plum-soft), var(--plum-mid) 75%); }

  .cover-photo { position: absolute; inset: 0; background:
      radial-gradient(ellipse at 28% 38%, var(--leather) 0%, #4a3038 38%, transparent 60%),
      linear-gradient(120deg, #3d2d38 0%, var(--plum-mid) 45%, var(--stone) 100%); }

  .brand { position: absolute; display: flex; flex-direction: column; align-items: center; font-family: "Oswald", sans-serif; font-weight: 300; color: var(--white); }
  .brand__dot { width: 64px; height: 64px; border-radius: 50%; background: var(--accent); margin-bottom: 6px; }
  .brand--front { top: 42px; right: 36px; font-size: 16px; }
  .brand--back { left: 452px; top: 350px; font-size: 12px; }
  .brand--back .brand__dot { width: 44px; height: 44px; margin-bottom: 4px; }

  .series-title { position: absolute; right: 30px; top: 296px; font-size: 104px; font-weight: 700; letter-spacing: -2px; line-height: 1; }
  .tagline-band { position: absolute; left: 0; right: 0; top: 423px; height: 87px; background: var(--plum-dark); display: flex; align-items: center; justify-content: center; }
  .tagline { font-family: "Noto Serif", serif; font-weight: 700; font-size: 46px; }

  .service-intro { position: absolute; top: 33px; width: 100%; text-align: center; font-size: 23px; font-weight: 700; }
  .service-time { position: absolute; top: 60px; width: 100%; text-align: center; font-size: 45px; font-weight: 800; letter-spacing: 1px; }

  .col-head { position: absolute; top: 136px; width: 238px; height: 59px; border-top: 2px solid var(--text-soft); border-bottom: 2px solid var(--text-soft); display: flex; align-items: center; justify-content: center; text-align: center; font-size: 22px; font-weight: 700; line-height: 1; letter-spacing: .5px; }
  .col-head--dates { left: 47px; }
  .col-head--features { left: 389px; }

  .list { position: absolute; top: 220px; list-style: none; font-family: "Comfortaa", sans-serif; font-weight: 500; font-size: 15px; color: var(--text-soft); }
  .list li { height: 25.6px; display: flex; align-items: center; white-space: pre; }
  .list li::before { content: "\2020"; font-family: "Open Sans", sans-serif; margin-right: 10px; }
  .list--dates { left: 42px; }
  .list--features { left: 426px; }
  .list--features li::before { margin-right: 14px; }

  .contact-band { position: absolute; left: 0; right: 0; bottom: 0; height: 73px; background: var(--plum-dark); text-align: center; display: flex; flex-direction: column; justify-content: center; gap: 4px; font-weight: 600; }
  .contact-band__address { font-size: 15px; }
  .contact-band__lines { font-size: 13.5px; }
</style>
</head>
<body>
  <section class="card card--front">
    <div class="cover-photo" role="img" aria-label="Photo of a closed leather Bible with a gold cross on its cover, resting on a stone surface"></div>
    <div class="brand brand--front"><span class="brand__dot"></span>Maplewood Family Church</div>
    <h1 class="series-title">Messy</h1>
    <div class="tagline-band"><p class="tagline">Joining God in the Mess</p></div>
  </section>

  <section class="card card--back">
    <p class="service-intro">The Time Of The Services,</p>
    <p class="service-time">Sundays @ 10:30</p>

    <h2 class="col-head col-head--dates">Dates &amp; Sermon<br>Names</h2>
    <h2 class="col-head col-head--features">Featuring</h2>

    <ul class="list list--dates">
      <li>April 28th : “We Made This Mess”</li>
      <li>May 5th    : “Bless in the Mess”</li>
      <li>May 12th : “Born into the Mess”</li>
      <li>May 19th : “Messy Work”</li>
      <li>May 26th : “Messy Church”</li>
      <li>June 2nd  : “Messy Hospitality”</li>
      <li>June 9th    :  TBD</li>
      <li>June 16th : “Messy within Boundaries”</li>
    </ul>

    <ul class="list list--features">
      <li>Staffed nursery</li>
      <li>children’s program</li>
      <li>Coffee &amp; snacks</li>
      <li>Everyone welcome</li>
    </ul>

    <div class="brand brand--back"><span class="brand__dot"></span>Maplewood Family Church</div>

    <footer class="contact-band">
      <p class="contact-band__address">Location – 1180 Cedar Line East Oakridge, ON L0K 2B3</p>
      <p class="contact-band__lines">Phone – 555.014.2290 | Email-info@maplewoodchurch.ca | Website-www.maplewoodchurch.ca</p>
    </footer>
  </section>
</body>
</html>
```